Equipment Finance Specialist I work with companies who need the funds to buy their equipment

I would like a business card that stands out on the shelves. I want to be able to hand it to someone and say WOW. This card should have my logo.
You can put color into it I am very open on design and color

What my company does is we deal with dealerships that sell equipment such as Dump Trucks garbage trucks tractors trailers. Customers get referred to us and depending on their time in business we will ask for the following items

Companies that have been in business for more than two years we have a credit application program up to 250K . With this program we need the following items Credit application filled out(which is what I would like to be able for the customer to click on my website to get.) as well as three current month bank statements.

Deals over 250k we will need the following items

2 years business tax returns
2 years personal tax returns
Profit & Loss statement
Personal Financial Statement

what we do
100% FINANCING
SEASONAL PAYMENTS
LOAN BALLOON PAYMENTS
TRAC LEASING
LOW-INTEREST REFINANCING RATES
DEBT CONSOLIDATION

We specialize in creative financing solutions and offer a variety of reliable, flexible and expandable lending choices.

Target Market(s)

Trucking Companies

Industry/Entity Type

Trucking Company

Contact Information for Business Card

* $250,000 Application only Program
* Loans from $30,000 to 5,000,000
* Competitive Interest Rates

Font styles to use
Serif
Sans Serif

Colors

Designer to choose colors to be used in the design.

Requirements
Must have
• On the back of the card.
• * $250,000 Application only Program
• * Loans from $30,000 to 5,000,000
• My name, email, website. address
• * Competitive Interest Rates
• * 100% Financing
Nice to have
• I want my logo to pop on the card
• My logo is the great one I would like to use
Should not have
• I am up for your creativity as well

```html
<!DOCTYPE html>
<html lang="en">
<head>
<meta charset="utf-8">
<title>Apex Lending – Business Card</title>
<link href="https://fonts.googleapis.com/css2?family=Open+Sans:wght@400;700&display=swap" rel="stylesheet">
<style>
  :root {
    --backdrop: #2b2b2d;
    --navy: #00286a;
    --crimson: #bf0d2e;
    --white: #ffffff;
  }
  * { margin: 0; padding: 0; box-sizing: border-box; }
  html, body {
    width: 1125px; height: 1200px; overflow: hidden;
    background: var(--backdrop);
    font-family: "Open Sans", Arial, sans-serif;
  }
  .card {
    position: absolute; left: 150px; width: 825px; height: 470px;
    overflow: hidden;
  }
  .card-front { top: 98px; background: var(--white); }
  .card-back { top: 630px; background: var(--crimson); }

  .contact-panel {
    position: absolute; left: 0; top: 0; bottom: 0; width: 346px;
    background: var(--navy); color: var(--white);
    padding: 118px 0 0 37px;
  }
  .person-name { font-size: 28px; font-weight: 700; line-height: 1.1; letter-spacing: 0.2px; }
  .person-title { font-size: 20px; line-height: 1.3; margin-bottom: 20px; }
  .address { font-size: 19px; line-height: 1.35; margin-bottom: 12px; }
  .contact-list { list-style: none; font-size: 19px; line-height: 1.42; }
  .contact-list li { display: flex; align-items: center; gap: 11px; }
  .contact-list svg { width: 19px; height: 19px; flex: none; fill: var(--white); }

  .accent-stripe {
    position: absolute; right: 0; top: 0; bottom: 0; width: 21px;
    background: var(--crimson);
  }
  .brand-front {
    position: absolute; left: 346px; right: 21px; top: 0; bottom: 0;
    display: flex; align-items: center; justify-content: center; gap: 14px;
  }
  .brand-dot { width: 34px; height: 34px; border-radius: 50%; background: var(--navy); }
  .brand-name {
    font-size: 44px; font-weight: 700; color: var(--navy);
    letter-spacing: 1px; text-transform: uppercase;
  }

  .brand-back {
    position: absolute; left: 0; right: 0; top: 150px;
    display: flex; align-items: center; justify-content: center; gap: 16px;
  }
  .brand-back .brand-dot { width: 40px; height: 40px; background: var(--white); }
  .brand-back .brand-name { color: var(--white); font-size: 52px; }

  .offer-lines {
    position: absolute; left: 0; right: 0; top: 392px;
    text-align: center; color: var(--white);
    font-size: 20px; line-height: 1.32;
  }
</style>
</head>
<body>
  <section class="card card-front">
    <div class="contact-panel">
      <h1 class="person-name">MARCUS HALE</h1>
      <p class="person-title">PRESIDENT</p>
      <p class="address">4127 Harbor View Lane<br>Glen Ridge, NY 11020</p>
      <ul class="contact-list">
        <li>
          <svg viewBox="0 0 24 24" aria-hidden="true"><path d="M6.6 10.8a15.1 15.1 0 0 0 6.6 6.6l2.2-2.2c.3-.3.7-.4 1-.2 1.1.4 2.3.6 3.6.6.6 0 1 .4 1 1V20c0 .6-.4 1-1 1C10.6 21 3 13.4 3 4c0-.6.4-1 1-1h3.5c.6 0 1 .4 1 1 0 1.3.2 2.5.6 3.6.1.3 0 .7-.2 1z"/></svg>
          <span>555 0142 7781</span>
        </li>
        <li>
          <svg viewBox="0 0 24 24" aria-hidden="true"><path d="M2 6l10 7 10-7v12H2z"/><path d="M2 4h20l-10 7z"/></svg>
          <span>marcus@apexlending.com</span>
        </li>
        <li>
          <svg viewBox="0 0 24 24" aria-hidden="true"><circle cx="12" cy="12" r="10"/><path d="M12 2a10 10 0 0 0 0 20M2 12h20" stroke="#00286a" stroke-width="1.6" fill="none"/></svg>
          <span>www.apexlending.com</span>
        </li>
      </ul>
    </div>
    <div class="brand-front">
      <span class="brand-dot"></span>
      <span class="brand-name">Apex Lending</span>
    </div>
    <div class="accent-stripe"></div>
  </section>

  <section class="card card-back">
    <div class="brand-back">
      <span class="brand-dot"></span>
      <span class="brand-name">Apex Lending</span>
    </div>
    <p class="offer-lines">
      $250,000 Application only Program &#9679; Loans from $30,000 to 5,000,000<br>
      Competitive Interest Rates &#9679;100% Financing
    </p>
  </section>
</body>
</html>
```